New Business Card Design for Manufacturing

We are an engineering/manufacturing company that offers Advanced machining/assembly/engineering services, as well as innovative products for the heavy duty engine cooling markets.

We are looking to get a new business card designed that is clean and modern looking, but still fits the wide range of technical/skilled work we do.

- We hope to use this design as the base for other design work in new Presentations, web, and print work.

Industry/Entity Type

Engineering

Contact Information for Business Card

Our preferred color of blue is (RGB) 22/71/159 but can vary slightly from that color. Our content will be our Logo and full company name (Vantrell Forge Works, Inc.), company address, name, job title, phone number with extension, cell number, fax number, website, and email address on the cards.
We'd like the full company name next to the logo, but we are open to other interpretations of that layout.
Preferably, we would like the back side to be clean with just our logo, and the front to contain all of the contact information.

Colors
2f74b4
0355a3
85abd2

Requirements
Must have
• - Logo, company name, needed content - We are open to interpretation beyond that.
• - Standard size business card.
• - Horizontal orientation.
• - Enough space for lengthy names / job titles (for example, a job title could read "Directory of Human Resources" or "V.P. of Governmental Affairs"). We need this to look clean, whether the title be short (CEO) or long (as described above).

```html
<!DOCTYPE html>
<html lang="en">
<head>
<meta charset="utf-8">
<title>Vantrell Forge Works, Inc. — Business Card</title>
<link rel="stylesheet" href="https://fonts.googleapis.com/css2?family=Roboto:wght@400;500;700;900&family=Roboto+Condensed:wght@700&display=swap">
<style>
  :root {
    --brand-blue: #0e4c96;
    --paper: #f2f2f2;
    --backdrop: #2b2b2b;
    --ink-dark: #1a1a1a;
    --ink-grey: #555555;
    --white: #ffffff;
  }
  * { margin: 0; padding: 0; box-sizing: border-box; }
  html, body {
    width: 1200px; height: 960px; overflow: hidden;
    background: var(--backdrop);
    font-family: "Roboto", Arial, sans-serif;
  }
  .canvas { position: relative; width: 1200px; height: 960px; }

  .card { position: absolute; width: 600px; height: 343px; }

  /* Front */
  .card-front { left: 314px; top: 113px; background: var(--paper); }
  .brand {
    position: absolute; left: 44px; top: 64px;
    display: flex; align-items: center; gap: 10px;
  }
  .brand-mark { width: 18px; height: 18px; background: var(--brand-blue); }
  .brand-name {
    font-weight: 700; font-size: 19px; line-height: 1.15;
    color: var(--brand-blue);
  }
  .holder { position: absolute; right: 46px; top: 67px; text-align: right; }
  .holder-name {
    font-family: "Roboto Condensed", "Arial Narrow", sans-serif;
    font-weight: 700; font-size: 27px; line-height: 1;
    color: var(--brand-blue); letter-spacing: 0.2px;
  }
  .holder-title { margin-top: 3px; font-size: 14px; color: var(--ink-dark); }

  .contact-band {
    position: absolute; left: 0; top: 176px; width: 100%; height: 118px;
    background: var(--brand-blue);
    padding: 20px 0 0 44px;
    list-style: none;
  }
  .contact-item {
    display: flex; align-items: center; height: 19px;
    font-size: 15px; color: var(--white);
  }
  .contact-item svg { width: 14px; height: 14px; margin-right: 9px; flex: none; }

  .address {
    position: absolute; left: 44px; top: 306px;
    font-size: 15px; color: var(--ink-grey);
  }

  /* Back */
  .card-back {
    left: 311px; top: 472px; background: var(--brand-blue);
    display: flex; flex-direction: column; align-items: center; justify-content: center;
    color: var(--white);
  }
  .back-name {
    font-weight: 900; font-size: 64px; line-height: 1; letter-spacing: 1px;
    text-transform: uppercase;
  }
  .back-tagline {
    margin-top: 12px; font-weight: 700; font-size: 19px;
    letter-spacing: 0.5px; text-transform: uppercase;
  }
</style>
</head>
<body>
<main class="canvas">

  <section class="card card-front" aria-label="Business card front">
    <div class="brand">
      <span class="brand-mark"></span>
      <span class="brand-name">Vantrell Forge<br>Works, Inc.</span>
    </div>

    <div class="holder">
      <p class="holder-name">CORIN HALVEY</p>
      <p class="holder-title">V.P. of Governmental Affairs</p>
    </div>

    <ul class="contact-band">
      <li class="contact-item">
        <svg viewBox="0 0 16 16" aria-hidden="true"><path fill="#fff" d="M3.6 1.2l2.3 2.6-1.4 1.7c.8 2 2.4 3.6 4.4 4.4l1.7-1.4 2.6 2.3-1.3 2.6C6.7 13.3 2.7 9.3 1 4.1z"/></svg>
        555 214 7730
      </li>
      <li class="contact-item">
        <svg viewBox="0 0 16 16" aria-hidden="true"><rect x="4" y="1" width="8" height="14" rx="1.5" fill="none" stroke="#fff" stroke-width="1.6"/><circle cx="8" cy="12.3" r="0.9" fill="#fff"/></svg>
        555 389 6142
      </li>
      <li class="contact-item">
        <svg viewBox="0 0 16 16" aria-hidden="true"><rect x="1.5" y="4" width="13" height="9" fill="#fff"/><path d="M1.5 4l6.5 5 6.5-5" fill="none" stroke="#0e4c96" stroke-width="1.2"/></svg>
        corin@vantrellforgeworks.com
      </li>
      <li class="contact-item">
        <svg viewBox="0 0 16 16" aria-hidden="true"><circle cx="8" cy="8" r="6.5" fill="#fff"/><path d="M5 4.5c1.5.5 1.2 2 2.6 2.4.9.3.4 1.8-.5 1.8-1 0-1.3 1.6-.5 2.6M10.5 3.5c-.6 1.2.4 1.8 1.4 2" fill="none" stroke="#0e4c96" stroke-width="1.1"/></svg>
        www.vantrellforgeworks.com
      </li>
    </ul>

    <p class="address">2916 Alderwood Court, Anchorage, Alaska 99507</p>
  </section>

  <section class="card card-back" aria-label="Business card back">
    <p class="back-name">Vantrell</p>
    <p class="back-tagline">Built to Endure</p>
  </section>

</main>
</body>
</html>
```